Brindlewood Elementary School 2019-2020 Priority Goals

This visual will encapsulate our school's annual goals. We are a large elementary school in a high performing school district. We base our annual goals primarily on our school generated set of foundational promises. We know that the relationships of the people are critical to our success. The product will primarily be used with our staff internally to keep focused on our priority goals for the year, which are to innovate and collaborate. The collaboration is both amongst staff and also in stronger partnerships with our parent community. The innovation is in not settling for how things have always been done and will focus in three areas: future ready skills, academic growth and achievement and finally in social/emotional growth. We have been saying to one another that "we will accelerate the academic and social emotional growth of the students we serve by innovating and collaborating.

Target Market(s)

Staff, parents and school board

Industry/Entity Type

Education

Font styles to use
Other font styles liked:
• open to your ideas

Colors
0255a3
fbed22

Requirements
Must have
• pretty new to this idea, we'll attach the early sketches below. You'll also find a school logo design as well as the promises that are referred to in the sketch.
Nice to have
• the colors below are school colors, but we are open to your creative genius as well.

```html
<!DOCTYPE html>
<html lang="en">
<head>
<meta charset="utf-8">
<title>Brindlewood Elementary School – 2019-2020 Priority Goals</title>
<link rel="stylesheet" href="https://fonts.googleapis.com/css2?family=Roboto+Condensed:wght@700&family=Montserrat:wght@500&family=Source+Sans+3:wght@400&display=swap">
<style>
  :root {
    --school-blue: #0255a3;
    --school-yellow: #fbed22;
  }
  html, body {
    margin: 0;
    padding: 0;
    width: 1200px;
    height: 1200px;
    overflow: hidden;
    background: var(--school-yellow);
  }
  .goals-poster {
    display: block;
    width: 1200px;
    height: 1200px;
  }
  .school-name {
    font-family: "Roboto Condensed", "Arial Narrow", sans-serif;
    font-weight: 700;
    fill: var(--school-blue);
  }
  .school-mark { fill: var(--school-blue); }
  .heart-fill { fill: var(--school-blue); }
  .heart-outline {
    fill: none;
    stroke: var(--school-blue);
    stroke-width: 5;
  }
  .outline-label {
    font-family: "Montserrat", sans-serif;
    font-weight: 500;
    font-size: 24px;
    letter-spacing: 1px;
    dominant-baseline: middle;
    text-anchor: middle;
  }
  .outline-knockout .outline-label {
    fill: var(--school-yellow);
    stroke: var(--school-yellow);
    stroke-width: 22px;
    stroke-linejoin: round;
  }
  .outline-labels .outline-label {
    fill: var(--school-blue);
  }
  .goal-text {
    font-family: "Roboto Condensed", "Arial Narrow", sans-serif;
    font-weight: 700;
    fill: var(--school-yellow);
    text-anchor: middle;
  }
  .goal-statement { font-size: 37px; }
  .goal-pillar { font-size: 40px; }
  .goal-detail { font-size: 28px; }
  .goal-detail.start { text-anchor: start; }
  .connector {
    stroke: var(--school-yellow);
    stroke-width: 2;
    fill: none;
  }
  .foundation-band { fill: var(--school-blue); }
  .foundation-frame {
    fill: none;
    stroke: var(--school-yellow);
    stroke-width: 5;
  }
  .foundation-title {
    font-family: "Source Sans 3", sans-serif;
    font-weight: 400;
    font-size: 50px;
    letter-spacing: -1.5px;
    fill: var(--school-yellow);
    text-anchor: middle;
  }
</style>
</head>
<body>
<svg class="goals-poster" viewBox="0 0 1500 1500" xmlns="http://www.w3.org/2000/svg" aria-labelledby="poster-title">
  <title id="poster-title">Brindlewood Elementary School priority goals</title>
  <defs>
    <path id="outline-top" d="M230,620 C230,470 320,355 480,355 C590,355 690,390 750,485 C810,390 910,355 1020,355 C1180,355 1270,470 1270,620"/>
    <path id="outline-bottom" d="M230,620 C230,840 420,1030 750,1328 C1080,1030 1270,840 1270,620"/>
  </defs>

  <g class="school-header">
    <circle class="school-mark" cx="750" cy="85" r="55"/>
    <text class="school-name" x="750" y="222" font-size="88" text-anchor="middle">BRINDLEWOOD</text>
    <text class="school-name" x="750" y="290" font-size="42" text-anchor="middle">ELEMENTARY SCHOOL</text>
  </g>

  <path class="heart-fill" d="M750,540 C700,440 600,385 480,385 C340,385 262,490 262,620 C262,820 450,1000 750,1290 C1050,1000 1238,820 1238,620 C1238,490 1160,385 1020,385 C900,385 800,440 750,540 Z"/>
  <use href="#outline-top" class="heart-outline"/>
  <use href="#outline-bottom" class="heart-outline"/>

  <g class="outline-knockout" aria-hidden="true">
    <text class="outline-label"><textPath href="#outline-top" startOffset="31%">Relationships</textPath></text>
    <text class="outline-label"><textPath href="#outline-top" startOffset="74%">Listen ! Every student has a song</textPath></text>
    <text class="outline-label"><textPath href="#outline-bottom" startOffset="11%">Mara Ellison</textPath></text>
    <text class="outline-label"><textPath href="#outline-bottom" startOffset="36%">Listening for student's song</textPath></text>
    <text class="outline-label"><textPath href="#outline-bottom" startOffset="66%">Mara Ellison</textPath></text>
    <text class="outline-label"><textPath href="#outline-bottom" startOffset="87%">Relationships</textPath></text>
  </g>
  <g class="outline-labels">
    <text class="outline-label"><textPath href="#outline-top" startOffset="31%">Relationships</textPath></text>
    <text class="outline-label"><textPath href="#outline-top" startOffset="74%">Listen ! Every student has a song</textPath></text>
    <text class="outline-label"><textPath href="#outline-bottom" startOffset="11%">Mara Ellison</textPath></text>
    <text class="outline-label"><textPath href="#outline-bottom" startOffset="36%">Listening for student's song</textPath></text>
    <text class="outline-label"><textPath href="#outline-bottom" startOffset="66%">Mara Ellison</textPath></text>
    <text class="outline-label"><textPath href="#outline-bottom" startOffset="87%">Relationships</textPath></text>
  </g>

  <text class="goal-text goal-statement" x="750" y="583">We will accelerate the</text>
  <text class="goal-text goal-statement" x="750" y="629">academic &amp; social/emotional growth</text>
  <text class="goal-text goal-statement" x="750" y="675">of the students we serve by :</text>

  <text class="goal-text goal-pillar" x="512" y="775">Innovating</text>
  <text class="goal-text goal-detail" x="512" y="806">Agents of change</text>
  <text class="goal-text goal-detail" x="512" y="833">Learners</text>
  <line class="connector" x1="422" y1="842" x2="422" y2="860"/>
  <line class="connector" x1="512" y1="842" x2="512" y2="860"/>
  <line class="connector" x1="602" y1="842" x2="602" y2="860"/>
  <text class="goal-text goal-detail" x="422" y="885">Social</text>
  <text class="goal-text goal-detail" x="512" y="885">Future</text>
  <text class="goal-text goal-detail" x="602" y="885">Ready</text>

  <text class="goal-text goal-pillar" x="721" y="775">And</text>

  <text class="goal-text goal-pillar" x="940" y="775">Collaborating</text>
  <polyline class="connector" points="892,829 940,782 988,829"/>
  <text class="goal-text goal-detail" x="881" y="856">Staff</text>
  <text class="goal-text goal-detail start" x="950" y="856">Parent</text>
  <text class="goal-text goal-detail start" x="950" y="881">Partnerships</text>
  <text class="goal-text goal-detail" x="928" y="916">Team</text>
  <text class="goal-text goal-detail" x="928" y="941">Players</text>

  <polygon class="foundation-band" points="405,1342 1092,1342 1132,1462 368,1462"/>
  <polygon class="foundation-frame" points="416,1354 1081,1354 1112,1450 388,1450"/>
  <text class="foundation-title" x="739" y="1424">Foundation Believe &amp; Promises</text>
</svg>
</body>
</html>
```